I need a letterhead for a newsletter that will go out quarterly to the dentists of the 18th district. It is called "The Crestline Digest" We are in Amarillo TX and have this landmark in the photo as our most prominent feature. If it could be used, that would be cool.
This is a professional organization newsletter so the letterhead should be somewhat professional.

Target Market(s)

Dentists

Industry/Entity Type

Dental

Font styles to use
Serif

Colors

Designer to choose only greyscale colors for use in the design.

Requirements
Must have
• I want the title of "The Crestline Digest" to be the on top with the phrase "Cobalt Ridge Dental Society" written underneath.
Nice to have
• the photo incorporated could be incorporated in black and white or color along the bottom of the letterhead or with the title inside the photo.
Should not have
• I don't want it to be cartoony. I want it to be stylish and elegant and professional.

```html
<!DOCTYPE html>
<html lang="en">
<head>
<meta charset="utf-8">
<title>The Crestline Digest – Letterhead</title>
<link rel="stylesheet" href="https://fonts.googleapis.com/css2?family=EB+Garamond:wght@400;700&family=Open+Sans:wght@400;700&family=Great+Vibes&display=swap">
<style>
  :root {
    --backdrop: #ecebe8;
    --paper: #ffffff;
    --ink: #111111;
    --ink-soft: #2a2a2a;
    --grey-title: #8a8a8a;
    --grey-contact: #444444;
    --rule: #333333;
    --wave-dark: #0d0d0d;
    --wave-grey: #7a7a7a;
  }
  * { margin: 0; padding: 0; box-sizing: border-box; }
  html, body {
    width: 1200px; height: 800px; overflow: hidden;
    background: var(--backdrop);
  }
  .letterhead {
    position: absolute;
    left: 330px; top: 18px;
    width: 540px; height: 764px;
    background: var(--paper);
    box-shadow: 0 2px 10px rgba(0,0,0,0.12);
    overflow: hidden;
    font-family: "Open Sans", Arial, sans-serif;
    color: var(--ink-soft);
  }
  .masthead {
    position: absolute; left: 70px; top: 44px; right: 52px;
  }
  .masthead__title {
    font-family: "EB Garamond", Georgia, serif;
    font-weight: 700;
    font-size: 27px;
    letter-spacing: 0.3px;
    color: var(--ink);
    line-height: 1;
    text-transform: uppercase;
  }
  .masthead__society {
    font-family: "EB Garamond", Georgia, serif;
    font-size: 15px;
    color: var(--grey-title);
    margin-top: 3px;
    line-height: 1;
  }
  .masthead__contact {
    font-family: "EB Garamond", Georgia, serif;
    font-size: 7.5px;
    color: var(--grey-contact);
    margin-top: 9px;
    display: flex;
    gap: 14px;
  }
  .masthead__contact span b { font-weight: 400; margin-right: 4px; }
  .masthead__rule {
    margin-top: 6px;
    border: 0;
    border-top: 1px solid var(--rule);
  }
  .letter__date {
    position: absolute; right: 60px; top: 218px;
    font-size: 8px; color: var(--ink);
  }
  .letter__body {
    position: absolute; left: 80px; right: 64px; top: 280px;
    font-size: 8px; line-height: 15.5px; color: var(--ink-soft);
  }
  .letter__body p + p { margin-top: 9px; }
  .signoff {
    position: absolute; left: 80px; top: 594px;
    color: var(--ink);
  }
  .signoff__signature {
    font-family: "Great Vibes", cursive;
    font-size: 20px; line-height: 1;
  }
  .signoff__name { font-size: 8px; font-weight: 700; margin-top: 3px; }
  .signoff__role { font-size: 8px; line-height: 1.1; }
  .footer-wave {
    position: absolute; left: 0; bottom: 0;
    width: 540px; height: 110px; display: block;
  }
  .footer-wave__dark { fill: var(--wave-dark); }
  .footer-wave__grey { fill: var(--wave-grey); }
  .footer__web {
    position: absolute; left: 0; right: 0; bottom: 64px;
    text-align: center;
    font-family: "EB Garamond", Georgia, serif;
    font-size: 9px; letter-spacing: 2px;
    color: var(--grey-contact);
    padding-left: 50px;
  }
</style>
</head>
<body>
  <main class="letterhead">
    <header class="masthead">
      <h1 class="masthead__title">The Crestline Digest</h1>
      <p class="masthead__society">Cobalt Ridge Dental Society</p>
      <p class="masthead__contact">
        <span><b>A :</b>410 W. Canyon Ave. Suite 200</span>
        <span><b>E:</b>info@cobaltridgedental.org</span>
        <span><b>P:</b>555-014-2290</span>
      </p>
      <hr class="masthead__rule">
    </header>

    <p class="letter__date">Date, 10 September, 2019</p>

    <section class="letter__body">
      <p>This is a sample letter that has been placed to demonstrate typing remat (Your Company). letterhead design. When positioned properly, it will serve to work in harmony with all other elements letterhead. This letterhead design is meant to project an image</p>
      <p>This letterhead design is meant project an image of professionalism reliability. By using simple aligen we have created a very spacious feeling. The simplicity suggest rengththe spaciousnes contributes h aesthetics the layout. These basic qualities along with the (Your Company)</p>
      <p>look and helps reinforce the (Your Company) brand. letterhead design is meant to project an image p design. When positioned properly, it will serve to work in harmony all the other elements letterhead. sionalism and reliability.</p>
      <p>This letterhead design is based on the (Form of your logo) form (Your Company) logo. Each stationery we have created a very spacious feeling. The simplicity suggests strength the spaciousnes contribute part of the (Form of your logo).</p>
    </section>

    <footer class="signoff">
      <p class="signoff__signature">Daniel Harrow</p>
      <p class="signoff__name">Daniel Harrow</p>
      <p class="signoff__role">Manager</p>
    </footer>

    <p class="footer__web">www.cobaltridgedental.org</p>
    <svg class="footer-wave" viewBox="0 0 540 110" aria-hidden="true">
      <path class="footer-wave__dark" d="M0,72 C110,38 250,52 370,74 C450,88 510,60 540,0 L540,110 L0,110 Z"/>
      <path class="footer-wave__grey" d="M0,84 C120,54 260,70 390,94 C460,106 515,96 540,62 L540,110 L0,110 Z"/>
    </svg>
  </main>
</body>
</html>
```